packaging design for disposable trash bag

We need 3 design for 3 of our products. first item is trash bag,the second item is disposable table cover and third is food packaging bag . We are a company in Singapore selling disposable product. This packaging products will be sold on shelf or online.

Attached is the requirement of the product. And some samples.

Target Market(s)

adult, most likely housewife

Requirements
Must have
• Packing design requirement for trash bag
• 1. Include company logo design, which is attached in the creative brief. DARVELLO POLYMER.
• 2. Clear showing of the product and its illustration of using. Eg. The trash bin.
• 3. Allocate a box for the purpose of sticking product size sticker.
• 4. Each packing bag holds 10pcs
• 5. Show of country of origin. Product of Singapore.
• 6. Use of one colour for printing of packing bag ( Black / blue/ bright Green/ white )
• 7. Show of warning: Keep polythene bags away from young children
• 8. dimension of the packagaing printing area : Lenght : 20 cm , Height 26 cm
• Packing design requirement for disposable Table Cover
• 1. Include company logo design, which is attached in the creative brief. Our company is DARVELLO POLYMER.
• 2. Clear showing of the product and its illustration of using. Eg. The table?.
• 4. Each packing bag holds 5pcs
• 6. Use of one colour for printing of the packing bag ( Black / blue/ bright Green )
• Packing design requirement for disposable food packaging plastic bag
• 2. Clear showing of the product and its illustration of using. Eg. Food?.
• 4. Show of country of origin. Product of Singapore.
• 5. Use of one colour for printing of the packing bag ( Black/ bright green )
• 6. Show of warning: Keep polythene bags away from young children
• 7. Show of product information: hygienic, food grade, freezer resistance, grease proof, damp proof, heat resistant.
• 8. Include the open here packing opening.
• 9. dimension of the packagaing printing area : Lenght : 15 cm , Height 22 cm
Nice to have
• requirement is stated in the must have. Good to allocate some space beside the packaging PCS area for promotion stickers . And also space allocated for bar code stickers.
Should not have
• no more than one color for printing

```html
<!DOCTYPE html>
<html lang="en">
<head>
<meta charset="utf-8">
<title>Darvello Polymer – Disposable Food Packaging Plastic Bag</title>
<link rel="stylesheet" href="https://fonts.googleapis.com/css2?family=Anton&family=Archivo+Black&family=Arimo:wght@400;700&family=Questrial&display=swap">
<style>
  :root {
    --ink: #111111;
    --paper: #ffffff;
    --food-tone: #2a2a2a;
  }
  html, body {
    margin: 0;
    padding: 0;
    width: 1200px;
    height: 790px;
    overflow: hidden;
    background: var(--paper);
  }
  .pack-face {
    display: block;
    width: 1200px;
    height: 790px;
  }
  .frame { fill: none; stroke: var(--ink); stroke-width: 9; stroke-linecap: butt; }
  .sticker-corner { fill: none; stroke: var(--ink); stroke-width: 4; }
  .open-window { fill: none; stroke: var(--ink); stroke-width: 6; }
  .tear-line { fill: none; stroke: var(--ink); stroke-width: 2; stroke-dasharray: 7 5; }
  .solid { fill: var(--ink); }
  .company-name { font-family: "Questrial", sans-serif; font-size: 38px; fill: var(--ink); }
  .title-small { font-family: "Archivo Black", sans-serif; font-size: 38px; fill: var(--ink); }
  .title-large { font-family: "Anton", sans-serif; font-size: 92px; fill: var(--ink); }
  .disposal-note { font-family: "Arimo", sans-serif; font-weight: 700; font-size: 10.5px; fill: var(--ink); }
  .feature { font-family: "Archivo Black", sans-serif; font-size: 15.5px; fill: var(--ink); }
  .label { font-family: "Arimo", sans-serif; font-weight: 700; font-size: 17.5px; fill: var(--ink); }
  .label-small { font-family: "Arimo", sans-serif; font-weight: 700; font-size: 12.5px; fill: var(--ink); }
  .open-label { font-family: "Arimo", sans-serif; font-weight: 700; font-size: 14.5px; fill: var(--ink); }
  .warning-head { font-family: "Archivo Black", sans-serif; font-size: 27px; fill: var(--ink); }
  .warning-line { font-family: "Arimo", sans-serif; font-weight: 700; font-size: 18.5px; fill: var(--ink); }
  .origin { font-family: "Arimo", sans-serif; font-size: 17.5px; fill: var(--ink); }
  .food-art { fill: var(--food-tone); }
</style>
</head>
<body>
<svg class="pack-face" viewBox="0 0 1500 987.5" xmlns="http://www.w3.org/2000/svg">

  <g class="brand">
    <rect class="solid" x="362" y="160" width="76" height="76"/>
    <text class="company-name" x="239" y="290" textLength="322" lengthAdjust="spacingAndGlyphs">DARVELLO POLYMER</text>
    <text class="company-name" x="400" y="328" text-anchor="middle">PTE LTD</text>
  </g>

  <g class="title-panel">
    <polyline class="frame" points="573,322 573,167 1229,167 1229,335"/>
    <text class="title-small" x="1211" y="221" text-anchor="end">DISPOSABLE</text>
    <text class="title-large" x="598" y="311" textLength="614" lengthAdjust="spacingAndGlyphs">FOOD PACKAGING PLASTIC BAG</text>
    <text class="disposal-note" x="598" y="358" textLength="635" lengthAdjust="spacingAndGlyphs">USED BAGS SHOULD BE DISPOSED OF IN A PROPER MANNER TO ENSURE CLEANLINESS TO THE SURROUNDING ENVIRONMENT.</text>
  </g>

  <g class="features">
    <polyline class="frame" points="233,385 233,352 580,352"/>
    <g class="feature-list">
      <rect class="solid" x="255" y="373" width="4" height="13"/><text class="feature" x="263" y="385">HYGENIC</text>
      <rect class="solid" x="255" y="392" width="4" height="13"/><text class="feature" x="263" y="404">FOOD GRADE</text>
      <rect class="solid" x="255" y="412" width="4" height="13"/><text class="feature" x="263" y="424">GREASE PROOF</text>
      <rect class="solid" x="255" y="431" width="4" height="13"/><text class="feature" x="263" y="443">DAMP PROOF</text>
      <rect class="solid" x="255" y="451" width="4" height="13"/><text class="feature" x="263" y="463">FREEZER RESISTANT</text>
      <rect class="solid" x="255" y="470" width="4" height="13"/><text class="feature" x="263" y="482">HEAT RESISTANT</text>
    </g>
  </g>

  <g class="open-here">
    <rect class="open-window" x="541" y="387" width="384" height="190" rx="30"/>
    <rect class="tear-line" x="553" y="399" width="360" height="166" rx="20"/>
    <polygon class="solid" points="894,446 894,418 866,418 872,423 889,423 889,440"/>
    <polygon class="solid" points="874,426 887,426 887,439"/>
    <text class="open-label" x="778" y="441">OPEN HERE</text>
    <polygon class="solid" points="567,517 567,549 599,549 593,544 572,544 572,523"/>
    <polygon class="solid" points="575,528 575,541 588,541"/>
    <text class="open-label" x="589" y="531">OPEN HERE</text>
  </g>

  <g class="usage">
    <rect class="food-art" x="964" y="384" width="258" height="88" rx="6" role="img" aria-label="Icons of a drink glass, a bowl of soup and a plate of noodles"/>
    <text class="label-small" x="1090" y="495" text-anchor="middle">SUITABLE FOR</text>
    <text class="label-small" x="1090" y="512" text-anchor="middle">MOST FOOD PACKAGING</text>
  </g>

  <g class="badges">
    <polygon class="solid" points="1018,546 1044,590 992,590"/>
    <rect class="solid" x="1056" y="548" width="40" height="40"/>
    <circle class="solid" cx="1135" cy="568" r="20"/>
    <rect class="solid" x="1168" y="548" width="36" height="40"/>
  </g>

  <g class="info-panel">
    <polyline class="frame" points="245,593 237,593 237,805 1230,805 1230,532 1136,532"/>

    <g class="barcode-space">
      <polyline class="sticker-corner" points="264,633 264,612 294,612"/>
      <polyline class="sticker-corner" points="573,612 603,612 603,641"/>
      <polyline class="sticker-corner" points="264,755 264,785 294,785"/>
      <polyline class="sticker-corner" points="573,785 603,785 603,755"/>
      <text class="label" x="433" y="703" text-anchor="middle">BARCODE</text>
    </g>

    <g class="warning">
      <text class="warning-head" x="732" y="650" text-anchor="middle">WARNING:</text>
      <text class="warning-line" x="732" y="677" text-anchor="middle">PLEASE KEEP</text>
      <text class="warning-line" x="732" y="700" text-anchor="middle">POLYTHENE BAGS</text>
      <text class="warning-line" x="732" y="724" text-anchor="middle">AWAY FROM</text>
      <text class="warning-line" x="732" y="747" text-anchor="middle">YOUNG CHILDREN</text>
      <text class="origin" x="732" y="783" text-anchor="middle">PRODUCT OF SINGAPORE</text>
    </g>

    <g class="size-space">
      <polyline class="sticker-corner" points="859,633 859,612 889,612"/>
      <polyline class="sticker-corner" points="1168,612 1198,612 1198,641"/>
      <polyline class="sticker-corner" points="859,755 859,785 889,785"/>
      <polyline class="sticker-corner" points="1168,785 1198,785 1198,755"/>
      <text class="label" x="1028" y="704" text-anchor="middle">SIZE (DIMENSION)</text>
    </g>
  </g>

</svg>
</body>
</html>
```